Dentistry Office

We want a new design for a Dentist's office website.

The theme is: "We provide high quality, state-of-the-art, dental care in a comfortable, caring environment."

The site currently has a menu on the left of the page with about 40 items on it. There is a great deal of textual content on each page, plus several illustrations.

We want to do this using CSS, so we need specifications in the CSS for all possible elements. The CSS needs to be named in a logical manner for easy use.

Every dentist on the planet seems to use lots of Flash. We don't want to because it is so distracting. We are looking for an elegant solution targeting 24-55 age group, but not excluding anyone.

The following (from another dentist's site) can give you a taste of what we want to communicate on the site:

"After 20 years of teaching dentists how to refine their technique and many years of writing textbooks, I currently devote my time to my office and the hands-on practice of dentistry. I'd like to welcome you personally to my dental practice, and I invite you to meet my highly experienced team of professionals.

"We have offered complete dental care of the highest quality since 1978. We provide Preventive Services, Tooth Whitening and Cosmetic Dentistry for a beautiful smile, Endodontics (root canal treatment) to treat painful teeth, Sedation Dentistry so you can relax, and Dental Implants to restore what is missing. We offer total care.

"Our approach to your health is simple: We use our education, experience and dedication to provide every patient with superior dental care.

"This passion for excellence is not just a goal, but a standard every member of our team holds.

"We also pride ourselves with our state of the art procedures, training and technology. This includes creating a beautiful smile using techniques that preserve as much of the original tooth as possible.

"Our abilities are renowned throughout the dental profession and I hope if you have any questions you will contact us by an e-mail note, by phone or just by dropping by."

Keep in mind the screen shape and dimensions. Your design needs to work in the normal screen proportions, regardless of how it looks when you post it here. Scrolling is OK, but the first impression needs to work.
Updates

Keep in mind that there will be about 250 words, or more, on each page.

Competitors web sites:

http://www.brindlecovedentist.example/

http://www.brindlecovedentalcare.example/

http://www.grinsbymarlowvaledental.example/

http://www.tenbyfamilydentalcare.example/

http://www.quelmardental.example/

http://www.dovrinadental.example/

We need to compete with these.

Target Market(s)

Generally adults seeking the most experienced and comfortable-to-be-with dentist.

Industry/Entity Type

Training

Requirements
Must have
• Must stand apart from other dentists.
• Must be elegant.
• Must have a horizontal menu structure across all columns, NOT a vertical that requires scrolling, no popout, pop down, etc. menus.
• We are looking for something special.
• Do not waste your time or ours putting up templates and things you have used before.
• Personally, I do not see how someone outside the US can understand the northern California dental market. But you are welcome to try.
Should not have
• Flash or graphics that move
• The look of a template
• Folksy fonts
• Looks like you used it 20 times before

```html
<!DOCTYPE html>
<html lang="en">
<head>
<meta charset="utf-8">
<title>Dentist's office</title>
<link rel="stylesheet" href="https://fonts.googleapis.com/css2?family=Arimo:wght@400;700&family=Didact+Gothic&display=swap">
<style>
:root{
  --page-bg:#cfe6f3;
  --page-bg-deep:#a9d1ea;
  --white:#ffffff;
  --navy:#0f4f7e;
  --blue:#1d73ad;
  --blue-light:#3f9bd3;
  --green:#7cb82f;
  --green-dark:#5a9416;
  --green-light:#a8d65a;
  --text:#555b61;
  --label:#4e565d;
  --red:#d8141c;
  --red-dark:#b00c12;
  --box-border:#c9d3da;
  --photo-a:#f3ede6;
  --photo-b:#d9e3ea;
  --photo-c:#e9d6c6;
}
*{box-sizing:border-box;margin:0;padding:0}
html,body{width:1200px;height:1074px;overflow:hidden}
body{
  position:relative;
  background:linear-gradient(180deg,var(--page-bg-deep) 0,var(--page-bg) 300px,var(--white) 420px,var(--white) 100%);
  font-family:"Arimo",Arial,sans-serif;color:var(--text);
}
.page{position:absolute;left:39px;top:27px;width:1122px;height:988px;background:var(--white)}
/* header */
.site-header{position:absolute;left:0;top:0;width:1122px;height:273px;overflow:hidden;background:var(--white)}
.header-photo{position:absolute;left:0;top:0;width:1122px;height:273px;
  background:linear-gradient(100deg,var(--photo-b) 0,var(--photo-a) 40%,var(--photo-c) 62%,var(--photo-a) 80%,#dfeef6 100%)}
.header-curve{position:absolute;left:0;top:0}
.brand{position:absolute;left:64px;top:66px;display:flex;align-items:center;gap:14px}
.brand-dot{width:30px;height:30px;border-radius:50%;background:var(--blue-light)}
.brand-name{font-family:"Didact Gothic",sans-serif;font-size:38px;line-height:1;color:var(--navy)}
.tagline{position:absolute;right:52px;top:18px;text-align:right;font-family:"Didact Gothic",sans-serif;color:var(--navy)}
.tagline-lead{font-size:23px;margin-right:60px}
.tagline-main{font-size:31px;margin-top:6px}
/* nav */
.main-nav{position:absolute;left:0;top:273px;width:1122px;height:59px;border-top:8px solid var(--navy);
  background:linear-gradient(180deg,var(--green-light) 0,var(--green) 45%,var(--green-dark) 100%)}
.main-nav ul{list-style:none;display:flex;height:51px}
.main-nav li{display:flex;align-items:center;justify-content:center;height:51px;
  font-family:"Didact Gothic",sans-serif;font-size:25px;color:var(--white);border-right:1px solid rgba(255,255,255,.45)}
.main-nav li:last-child{border-right:0}
.main-nav .is-active{background:linear-gradient(180deg,var(--blue-light),var(--blue));}
/* sidebar */
.side-box{position:absolute;left:18px;width:290px;border:1px solid var(--box-border);border-radius:16px;
  background:linear-gradient(180deg,#fff 0,#f3f5f7 100%);box-shadow:0 2px 4px rgba(0,0,0,.12)}
.side-box-title{position:relative;height:44px;border-radius:14px 14px 0 0;overflow:hidden;
  background:linear-gradient(180deg,var(--blue-light),var(--blue));color:var(--white);
  font-family:"Didact Gothic",sans-serif;font-size:25px;line-height:44px;padding-left:64px}
.side-box-title svg{position:absolute;left:14px;top:0}
.services-box{top:342px;height:290px}
.services-list{list-style:none;padding:14px 0 0 12px;font-size:15.5px;line-height:21px;color:var(--label)}
.services-list li{margin-bottom:10px;width:190px}
.services-list li.wide{width:260px}
.kit-figure{position:absolute;right:10px;top:56px;width:88px;height:92px;border-radius:8px;
  background:linear-gradient(160deg,#e8ecef,#9aa3aa)}
.btn-red{position:absolute;display:flex;align-items:center;justify-content:center;color:var(--white);font-weight:700;
  font-size:15.5px;background:linear-gradient(180deg,#ee2a31,var(--red-dark));border-radius:2px}
.view-more{right:24px;top:246px;width:105px;height:30px}
.appointment-box{top:644px;height:292px}
.appointment-form{padding:20px 0 0 12px}
.form-row{display:flex;align-items:center;height:39px}
.form-row label{width:62px;font-size:15.5px;color:var(--label)}
.form-row span{display:block;width:102px;height:23px;border:1px solid var(--box-border);background:var(--white)}
.clock-figure{position:absolute;left:186px;top:62px;width:90px;height:60px;border-radius:10px;
  background:linear-gradient(135deg,#cfeaf7,#7fc0e4 60%,#9ccd6a)}
.send{left:160px;top:256px;width:106px;height:30px}
/* content */
.content{position:absolute;left:323px;top:344px;width:786px;height:574px;border:1px solid #e3e8ec;border-radius:22px;
  background:var(--white);box-shadow:0 4px 8px rgba(0,0,0,.12);padding:26px 0 0 24px}
.content h1{font-weight:700;font-size:33px;color:var(--navy);letter-spacing:-.3px}
.content h1 .accent{font-family:"Didact Gothic",sans-serif;font-weight:400;font-size:43px;color:var(--green-dark);letter-spacing:0}
.content p{font-size:15.5px;color:var(--text);margin-top:10px}
.content .intro{line-height:25.5px;margin-top:20px;width:720px}
.content .services-text{line-height:31px;margin-top:20px}
.content .approach{line-height:30px;margin-top:18px;width:720px}
.content .line{line-height:27px;margin-top:8px}
/* footer */
.site-footer{position:absolute;left:39px;top:1015px;width:1122px;height:59px;border-top:8px solid var(--navy);
  background:linear-gradient(180deg,var(--green-light),var(--green) 50%,var(--green-dark));
  display:flex;justify-content:space-between;align-items:center;padding:0 20px 0 20px;color:var(--white);font-size:15px}
.footer-links{display:flex;gap:8px}
.footer-links span+span::before{content:"|";margin-right:8px}
</style>
</head>
<body>
<div class="page">
  <header class="site-header">
    <div class="header-photo" role="img" aria-label="Photo of a smiling family with a dentist holding an apple"></div>
    <svg class="header-curve" width="500" height="273" viewBox="0 0 500 273" aria-hidden="true">
      <path d="M0 0 H450 C430 120 300 230 0 250 Z" fill="#ffffff"/>
      <path d="M450 0 C430 120 300 230 0 250" fill="none" stroke="#0f4f7e" stroke-width="4"/>
      <path d="M465 0 C445 135 310 245 0 262" fill="none" stroke="#9fd0ec" stroke-width="6"/>
    </svg>
    <div class="brand"><span class="brand-dot"></span><span class="brand-name">Dentist's office</span></div>
    <div class="tagline"><div class="tagline-lead">Definitely something to</div><div class="tagline-main">Smile about.</div></div>
  </header>

  <nav class="main-nav">
    <ul>
      <li style="width:120px">Home</li>
      <li class="is-active" style="width:150px">About us</li>
      <li style="width:155px">Services</li>
      <li style="width:175px">Our Team</li>
      <li style="width:213px">Appointment</li>
      <li style="width:155px">Practice</li>
      <li style="width:154px">Contact</li>
    </ul>
  </nav>

  <aside class="side-box services-box">
    <h2 class="side-box-title"><svg width="40" height="44" aria-hidden="true"><path d="M14 44 L30 0 H38 L22 44Z M0 44 L16 0 H24 L8 44Z" fill="#ffffff" opacity=".85"/></svg>Our Services</h2>
    <ul class="services-list">
      <li>Biomimetic approach</li>
      <li>Children's dentistry</li>
      <li>Treatment for nervous patients</li>
      <li class="wide">Minimally Invasive Dentistry</li>
      <li class="wide">Regular "check-up" and hygiene visits</li>
    </ul>
    <div class="kit-figure" role="img" aria-label="Silver first-aid case with a red cross"></div>
    <div class="btn-red view-more">View More..</div>
  </aside>

  <aside class="side-box appointment-box">
    <h2 class="side-box-title"><svg width="40" height="44" aria-hidden="true"><path d="M14 44 L30 0 H38 L22 44Z M0 44 L16 0 H24 L8 44Z" fill="#ffffff" opacity=".85"/></svg>Appointment</h2>
    <div class="appointment-form">
      <div class="form-row"><label>Doctor:</label><span></span></div>
      <div class="form-row"><label>Type:</label><span></span></div>
      <div class="form-row"><label>City:</label><span></span></div>
      <div class="form-row"><label>Name:</label><span></span></div>
      <div class="form-row"><label>Phone:</label><span></span></div>
    </div>
    <div class="clock-figure" role="img" aria-label="Appointment list with a clock"></div>
    <div class="btn-red send">Send</div>
  </aside>

  <main class="content">
    <h1>Welcome to <span class="accent">Dentist office</span></h1>
    <p class="intro">After 20 years of teaching dentists how to refine their technique and many years of writing textbooks, I currently devote my time to my office and the hands-on practice of dentistry. to welcome you personally to my dental practice, and I invite you to meet my highly experienced team of professionals.</p>
    <p class="services-text">We have offered complete dental care of the highest quality since 1978. We provide Preventive Services, Tooth Whitening and Cosmetic Dentistry for a beautiful smile,Endodontics (root canal treatment) to treat painful teeth, Sedation Dentistry so you can relax,and Dental Implants to restore what is missing. We offer total care.</p>
    <p class="approach">Our approach to your health is simple: We use our education, experience and dedication to provide every patient with superior dental care.</p>
    <p class="line">This passion for excellence is not just a goal, but a standard every member of our team holds.</p>
    <p class="line">We also pride ourselves with our state of the art procedures, training and technology.<br>This includes creating a beautiful smile using techniques that preserve as much of the original tooth as possible.</p>
  </main>
</div>

<footer class="site-footer">
  <span>copyright 2010 &nbsp;by Dentist office All rights reserved.</span>
  <div class="footer-links"><span>Home</span><span>About us</span><span>Services</span><span>Our Team</span><span>Appointment</span><span>Practice</span><span>Contact us</span></div>
</footer>
</body>
</html>
```